Private Investment Firm Needs PowerPoint Presentation Template

Design PowerPoint template, take Pinebrook-submitted rough presentation draft, and drop it into new template. See attached Project Brief file for more detail.
Updates

Some decent designs have been submitted but they seem to lack the understanding of our target markets. I am hopeful that more time and feedback will result in better results.

Target Market(s)

Private company owners and intermediaries.

Font styles to use
Serif

Colors
3176b5

Requirements
Must have
• See attached Project Brief.
Nice to have
Should not have
• No B2C fluff--this is a B2B project.

```html
<!DOCTYPE html>
<html lang="en">
<head>
<meta charset="utf-8">
<title>The 12 Primary Uses of Non-Control Capital</title>
<link rel="stylesheet" href="https://fonts.googleapis.com/css2?family=Nunito:wght@400;600;700;800&display=swap">
<style>
  :root {
    --brand-blue: #1268b3;
    --title-blue: #1466b0;
    --row-dark: #0f6cb6;
    --row-light: #5aa7dc;
    --row-mid: #3a8fd3;
    --accent-gray: #55585c;
    --slide-top: #ffffff;
    --slide-bottom: #e6e8eb;
    --ink: #1b1b1b;
    --white: #ffffff;
  }
  * { margin: 0; padding: 0; box-sizing: border-box; }
  html, body { width: 1200px; height: 770px; overflow: hidden; }
  body { font-family: "Nunito", sans-serif; }

  .slide {
    position: relative;
    width: 1200px;
    height: 770px;
    background: linear-gradient(135deg, var(--slide-top) 30%, var(--slide-bottom) 100%);
    overflow: hidden;
  }
  .slide-shapes { position: absolute; inset: 0; }

  .slide-title {
    position: absolute;
    top: 84px; left: 0; right: 0;
    text-align: center;
    font-weight: 800;
    font-size: 40px;
    letter-spacing: 0.3px;
    color: var(--title-blue);
  }
  .title-rule {
    position: absolute;
    top: 146px; left: 571px;
    width: 58px; height: 5px;
    border-radius: 3px;
    background: var(--title-blue);
  }

  .uses-grid {
    position: absolute;
    top: 178px; left: 146px;
    width: 907px;
    display: grid;
    grid-template-columns: repeat(4, 223px);
    grid-template-rows: repeat(3, 153px);
    column-gap: 5px;
  }
  .use-card {
    position: relative;
    display: flex;
    flex-direction: column;
    align-items: center;
    justify-content: center;
    padding: 0 18px 10px;
    text-align: center;
    color: var(--white);
  }
  .use-card::after {
    content: "";
    position: absolute;
    left: 50%; bottom: -11px;
    transform: translateX(-50%);
    border-left: 11px solid transparent;
    border-right: 11px solid transparent;
    border-top: 11px solid var(--card-bg);
    z-index: 2;
  }
  .row-1 { --card-bg: var(--row-dark); background: var(--row-dark); }
  .row-2 { --card-bg: var(--row-light); background: var(--row-light); }
  .row-3 { --card-bg: var(--row-mid); background: var(--row-mid); }

  .use-title {
    font-weight: 800;
    font-size: 16px;
    line-height: 1.2;
    letter-spacing: 0.3px;
    margin-bottom: 10px;
  }
  .use-text {
    font-size: 10.5px;
    line-height: 1.2;
  }

  .brand-mark {
    position: absolute;
    top: 668px; left: 122px;
    display: flex;
    align-items: center;
    gap: 10px;
    color: var(--brand-blue);
    font-weight: 800;
  }
  .brand-dot {
    width: 40px; height: 40px;
    border-radius: 50%;
    background: var(--brand-blue);
  }
  .brand-name { font-size: 20px; letter-spacing: 2px; line-height: 1.1; display: block; }
  .brand-tagline { font-size: 7px; letter-spacing: 0.8px; text-transform: uppercase; display: block; }

  .site-url {
    position: absolute;
    top: 680px; left: 0; width: 1496px;
    text-align: center;
    font-size: 19px;
    color: var(--ink);
  }
  .site-url strong { color: var(--brand-blue); font-weight: 800; }

  .page-number {
    position: absolute;
    top: 683px; left: 1099px;
    font-weight: 800;
    font-size: 15px;
    color: var(--white);
  }
</style>
</head>
<body>
<main class="slide">
  <svg class="slide-shapes" width="1200" height="770" viewBox="0 0 1200 770" aria-hidden="true">
    <defs>
      <linearGradient id="edge-blue" x1="0" y1="0" x2="1" y2="0">
        <stop offset="0" stop-color="#2a8ad6"/>
        <stop offset="1" stop-color="#0b5fa8"/>
      </linearGradient>
    </defs>
    <polygon points="0,0 106,0 0,504" fill="var(--accent-gray)"/>
    <polygon points="1171,0 1200,0 1200,770 982,770" fill="url(#edge-blue)"/>
  </svg>

  <h1 class="slide-title">The 12 Primary Uses of Non-Control Capital</h1>
  <div class="title-rule"></div>

  <section class="uses-grid">
    <article class="use-card row-1">
      <h2 class="use-title">Growth</h2>
      <p class="use-text">Capital used to organically expand a business: introduce new products, build a new factory, hire additional management or employees, enter new markets, or for general working capital purposes</p>
    </article>
    <article class="use-card row-1">
      <h2 class="use-title">Acquisitions</h2>
      <p class="use-text">Capital used to acquire one or more competitors or to allow for further vertical or horizontal integration</p>
    </article>
    <article class="use-card row-1">
      <h2 class="use-title">Partner or Shareholder Buy-Out</h2>
      <p class="use-text">Capital used to buy-out an inactive or retiring partner or shareholder</p>
    </article>
    <article class="use-card row-1">
      <h2 class="use-title">Management Buy-Out (MBO)</h2>
      <p class="use-text">When the incumbent management team buys most or all of the ownership of an inactive founder or executive</p>
    </article>

    <article class="use-card row-2">
      <h2 class="use-title">Management Buy-In (MBI)</h2>
      <p class="use-text">When an external, experienced executive buys a business from one or more inactive owners and needs additional capital to affect the purchase</p>
    </article>
    <article class="use-card row-2">
      <h2 class="use-title">Family Ownership &amp; Wealth Transfer</h2>
      <p class="use-text">When junior generations of a family acquire most or all of the ownership interests of more senior generations allowing the business to remain in the family name</p>
    </article>
    <article class="use-card row-2">
      <h2 class="use-title">Balance Sheet Recapitalization</h2>
      <p class="use-text">Changes the debt and equity mixture of a Company's finances to a more optimal capital structure</p>
    </article>
    <article class="use-card row-2">
      <h2 class="use-title">Refinancing</h2>
      <p class="use-text">Replacing one form or type of debt with another with better terms, conditions, and flexibility</p>
    </article>

    <article class="use-card row-3">
      <h2 class="use-title">Family Office Support</h2>
      <p class="use-text">Allows a Family Office to affect an investment in a Company by allowing a junior capital provider to invest alongside them</p>
    </article>
    <article class="use-card row-3">
      <h2 class="use-title">Senior Lender Enhancement or Transition</h2>
      <p class="use-text">When a Company has grown beyond the means or interest of its senior bank but needs additional capital to support its continuing growth</p>
    </article>
    <article class="use-card row-3">
      <h2 class="use-title">De-Lever Balance Sheet</h2>
      <p class="use-text">When a Company has taken on too much debt (typically senior debt) and replaces some of it with either equity or other junior capital to provide operating flexibility</p>
    </article>
    <article class="use-card row-3">
      <h2 class="use-title">Owner Dividend (Liquidity)</h2>
      <p class="use-text">When one or more owners take a non-life changing cash distribution, typically used to diversify their net worth</p>
    </article>
  </section>

  <div class="brand-mark">
    <span class="brand-dot"></span>
    <span>
      <span class="brand-name">PINEBROOK</span>
      <span class="brand-tagline">Non-Control Growth Capital</span>
    </span>
  </div>

  <p class="site-url">www.<strong>pinebrookgrowth</strong>.example</p>
  <p class="page-number">5.</p>
</main>
</body>
</html>
```